High-end law practice specializing in closely held business succession planning and complex estates

Solo practitioner whose practice specializes in high-net worth, complex estate planning needs muliple versions of letterhead black and white, please. Letterhead should incorporate slogan, "Protecting your family business is my business," for one and "Complex Estate Planning"; third with no slogan. All for The Law Office of Marcy Lynn Pettibone, PC, 418 Cedar Hollow Ln., Newport News, Virginia 23648, Tel. 757-555-0142 Fax tbd email: marcy@mlplawgroup.example; Marcy Lynn Pettibone, Esq., principal, licensed in VA, NY, DC
Updates

Project Deadline Extended
Reason: My internet service went down and I can only view designs on my smart phone -- it's just too hard to review. So sorry! Working with my ISP now. Please be patient!

Target Market(s)

High net worth clients with complex estate planning needs, family businesses, family farmers, family foresters -- people with unique estate/succession planning needs who need a specialist who understands them.

Industry/Entity Type

Business

Font styles to use
Script

Requirements
Must have
• A high-end look and feel, connoting trustworthiness, special knowledge, and expertise.

```html
<!DOCTYPE html>
<html lang="en">
<head>
<meta charset="utf-8">
<title>Letterhead – The Law Office of Marcy Lynn Pettibone, PC</title>
<link rel="stylesheet" href="https://fonts.googleapis.com/css2?family=Crimson+Pro:wght@400;600&display=swap">
<style>
  :root {
    --backdrop: #cfcfcf;
    --paper: #f0f0f0;
    --ink: #1e1e1e;
    --rule: #555555;
    --band-grey: #9a9a9a;
    --band-dark: #232323;
  }
  * { margin: 0; padding: 0; box-sizing: border-box; }
  html, body {
    width: 1200px; height: 1041px; overflow: hidden;
    background: var(--backdrop);
    font-family: "Crimson Pro", Georgia, serif;
    color: var(--ink);
  }
  .letterhead {
    position: absolute; left: 280px; top: 106px;
    width: 640px; height: 827px;
    background: var(--paper);
  }
  .firm-name {
    position: absolute; left: 40px; top: 54px;
    font-weight: 400; color: var(--ink); line-height: 1;
  }
  .firm-name .line-main { display: block; font-size: 22px; }
  .firm-name .line-sub { display: block; font-size: 11px; letter-spacing: 0.03em; text-transform: uppercase; margin-top: 3px; padding-left: 2px; }
  .contact-block {
    position: absolute; top: 56px; right: 32px;
    display: flex; align-items: flex-start;
  }
  .contact {
    font-size: 8.2px; line-height: 10.3px;
  }
  .contact p { white-space: nowrap; }
  .contact strong { font-weight: 600; }
  .contact-lines { margin-left: 10px; padding-left: 9px; border-left: 0.8px solid var(--rule); }
  .contact-address { margin-left: 10px; padding-left: 10px; border-left: 0.8px solid var(--rule); }
  .footer-band { position: absolute; left: 0; bottom: 0; width: 640px; height: 17px; }
</style>
</head>
<body>
  <main class="letterhead">
    <header>
      <div class="firm-name">
        <span class="line-main">The Law Office</span>
        <span class="line-sub">of Marcy Lynn Pettibone, PC</span>
      </div>
      <div class="contact-block">
        <div class="contact contact-person">
          <p><strong>Marcy Lynn Pettibone</strong>, Esq.</p>
          <p>Principal</p>
          <p>Licensed in VA, NY, DC</p>
        </div>
        <div class="contact contact-lines">
          <p>T: 757-555-0142</p>
          <p>F: 757-555-0143</p>
          <p>E: marcy@mlplawgroup.example</p>
        </div>
        <div class="contact contact-address">
          <p>418 Cedar Hollow Ln.</p>
          <p>Newport News</p>
          <p>Virginia 23648</p>
        </div>
      </div>
    </header>
    <svg class="footer-band" viewBox="0 0 640 17" aria-hidden="true">
      <polygon points="0,6.4 421.6,6.4 412.8,17 0,17" fill="var(--band-grey)"/>
      <polygon points="438.4,0 640,0 640,17 424,17" fill="var(--band-dark)"/>
    </svg>
  </main>
</body>
</html>
```